A clean crisp business card for a Landscape Construction company. Designed to be easy to read contact/ info and also be appealing/interesting, unlike a traditional business card.

Industry/Entity Type

Landscape Construction

Contact Information for Business Card

Company name : Brambleford Landscape Construction, phone number: (877) 62Vista, website:Bramblefordyards.example, Email, sales@bramblefordyards.example

Requirements
Nice to have
• Luxurious finishes/ details…. Icons or emblems next to contact info
Should not have
• Clipart or general pictures

```html
<!DOCTYPE html>
<html lang="en">
<head>
<meta charset="utf-8">
<title>Brambleford Landscape Construction – Business Card</title>
<link rel="stylesheet" href="https://fonts.googleapis.com/css2?family=Cinzel:wght@500;600&family=Open+Sans:wght@400;600&display=swap">
<style>
  :root {
    --brand-blue: #2367b4;
    --brand-green: #8cc63f;
    --ink: #1f1f1f;
    --paper: #ffffff;
    --backdrop: #e4e6e8;
  }
  * { box-sizing: border-box; margin: 0; padding: 0; }
  html, body { width: 1200px; height: 928px; overflow: hidden; background: var(--backdrop); }
  .canvas { position: relative; width: 1200px; height: 928px; }
  .card {
    position: absolute;
    background: var(--paper);
    border-radius: 16px;
    overflow: hidden;
    box-shadow: 0 6px 18px rgba(0,0,0,0.18);
  }
  .card--front { left: 267px; top: 59px; width: 670px; height: 382px; }
  .card--back  { left: 264px; top: 484px; width: 676px; height: 387px; }

  .wordmark {
    position: absolute;
    font-family: "Cinzel", serif;
    font-weight: 600;
    color: var(--brand-blue);
    text-align: center;
    line-height: 1;
  }
  .wordmark__name { display: block; }
  .wordmark__tag { display: block; letter-spacing: 0.18em; }
  .card--front .wordmark { left: 0; right: 0; top: 180px; }
  .card--front .wordmark__name { font-size: 50px; }
  .card--front .wordmark__tag { font-size: 17px; margin-top: 10px; }
  .card--back .wordmark { left: 360px; width: 300px; top: 120px; }
  .card--back .wordmark__name { font-size: 33px; }
  .card--back .wordmark__tag { font-size: 11.5px; margin-top: 6px; }

  .front-url {
    position: absolute; left: 0; right: 0; top: 334px;
    text-align: center;
    font-family: "Cinzel", serif; font-weight: 600; font-size: 16px;
    letter-spacing: 0.06em;
    color: var(--brand-blue);
  }
  .front-url__accent { color: var(--brand-green); }

  .person { position: absolute; left: 41px; top: 40px; }
  .person__name {
    font-family: "Cinzel", serif; font-weight: 600; font-size: 28px;
    letter-spacing: 0.04em; color: var(--brand-blue);
  }
  .person__name-last { color: var(--brand-green); margin-left: 10px; }
  .person__role {
    font-family: "Open Sans", sans-serif; font-size: 15px; color: var(--ink);
    margin-top: 4px; letter-spacing: 0.02em;
  }

  .contacts { position: absolute; left: 41px; top: 200px; list-style: none; }
  .contacts__item {
    display: flex; align-items: center; gap: 7px;
    height: 32.5px;
    font-family: "Open Sans", sans-serif; font-size: 15px; color: var(--ink);
  }
  .contacts__icon { width: 17px; height: 17px; fill: var(--brand-blue); flex: none; }

  .wave { position: absolute; left: 0; top: 0; width: 676px; height: 387px; }

  .address {
    position: absolute; right: 32px; top: 308px;
    text-align: right;
    font-family: "Open Sans", sans-serif; font-weight: 600; font-size: 15.5px;
    line-height: 27px; color: var(--paper);
  }
</style>
</head>
<body>
<main class="canvas">

  <section class="card card--front" aria-label="Card front">
    <div class="wordmark">
      <span class="wordmark__name">Brambleford</span>
      <span class="wordmark__tag">Landscape Construction</span>
    </div>
    <p class="front-url">www.<span class="front-url__accent">Bramblefordyards</span>.example</p>
  </section>

  <section class="card card--back" aria-label="Card back">
    <svg class="wave" viewBox="0 0 676 387" aria-hidden="true">
      <path d="M0,270 C90,345 200,362 310,356 C440,348 560,282 676,280 L676,387 L0,387 Z" fill="var(--brand-blue)"/>
      <path d="M50,306 C130,352 230,364 320,350 C450,332 560,268 660,268" fill="none" stroke="var(--paper)" stroke-width="9"/>
      <path d="M50,306 C130,352 230,364 320,350 C450,332 560,268 660,268" fill="none" stroke="var(--brand-green)" stroke-width="5"/>
    </svg>

    <div class="person">
      <p class="person__name">Elliot<span class="person__name-last">Marsh</span></p>
      <p class="person__role">Director</p>
    </div>

    <div class="wordmark">
      <span class="wordmark__name">Brambleford</span>
      <span class="wordmark__tag">Landscape Construction</span>
    </div>

    <ul class="contacts">
      <li class="contacts__item">
        <svg class="contacts__icon" viewBox="0 0 24 24" aria-hidden="true"><path d="M6.6 10.8a15.1 15.1 0 0 0 6.6 6.6l2.2-2.2a1 1 0 0 1 1-.25 11.4 11.4 0 0 0 3.6.57 1 1 0 0 1 1 1V20a1 1 0 0 1-1 1A17 17 0 0 1 3 4a1 1 0 0 1 1-1h3.5a1 1 0 0 1 1 1c0 1.25.2 2.45.57 3.57a1 1 0 0 1-.25 1z"/></svg>
        <span>(877) 62Vista</span>
      </li>
      <li class="contacts__item">
        <svg class="contacts__icon" viewBox="0 0 24 24" aria-hidden="true"><path d="M2 5h20v14H2z M3.5 6.5 12 13l8.5-6.5" fill="var(--brand-blue)"/><path d="M3 6.5 12 13l9-6.5" fill="none" stroke="var(--paper)" stroke-width="1.6"/></svg>
        <span>sales@bramblefordyards.example</span>
      </li>
      <li class="contacts__item">
        <svg class="contacts__icon" viewBox="0 0 24 24" aria-hidden="true"><circle cx="12" cy="12" r="10"/><path d="M2 12h20M12 2c3 3 3 17 0 20M12 2c-3 3-3 17 0 20" fill="none" stroke="var(--paper)" stroke-width="1.4"/></svg>
        <span>www.bramblefordyards.example</span>
      </li>
    </ul>

    <address class="address">
      4120 Alder Creek Rd<br>
      NUM 118, Fairview, OH 45000
    </address>
  </section>

</main>
</body>
</html>
```